Business Card Design

We are looking for a business card designed for our landscaping company. We do landscaping installation & Maintenance Services. We would like to see designs that have basic landscaping in background. We also think it is important to have both of our names and phone numbers on the card. We need something that stands out a little whether it is shape of the card or thickness or design.

Business

Bramblewood Yardworks, bramblewoodyard@mailvista.net, Owen Platt 555-273-9104, Daniel Korbin 555-618-3927

```html
<!DOCTYPE html>
<html lang="en">
<head>
<meta charset="utf-8">
<title>Bramblewood Yardworks – Business Card</title>
<link rel="stylesheet" href="https://fonts.googleapis.com/css2?family=PT+Sans:wght@400&display=swap">
<style>
  :root {
    --backdrop: #cbcbcb;
    --card: #ffffff;
    --leaf: #1ee61e;
    --ink: #111111;
    --on-leaf: #ffffff;
  }
  * { margin: 0; padding: 0; box-sizing: border-box; }
  html, body {
    width: 1200px;
    height: 754px;
    overflow: hidden;
    background: var(--backdrop);
    font-family: "PT Sans", "Myriad Pro", sans-serif;
  }
  .card {
    position: absolute;
    left: 84px;
    top: 72px;
    width: 1033px;
    height: 608px;
    background: var(--card);
    overflow: hidden;
  }
  .top-tab {
    position: absolute;
    left: 53px;
    top: 0;
    width: 148px;
    height: 70px;
  }
  .footer-band {
    position: absolute;
    left: 0;
    top: 456px;
    width: 100%;
    height: 152px;
    background: var(--leaf);
  }
  .footer-notch {
    position: absolute;
    left: 84px;
    top: 0;
    width: 89px;
    height: 38px;
  }
  .company {
    position: absolute;
    left: 61px;
    top: 138px;
    font-size: 78px;
    line-height: 104px;
    letter-spacing: 0.5px;
    text-transform: uppercase;
  }
  .company-line-1 { display: block; color: var(--ink); }
  .company-line-2 { display: block; color: var(--leaf); }
  .divider {
    position: absolute;
    left: 657px;
    top: 152px;
    width: 5px;
    height: 172px;
    background: var(--leaf);
  }
  .contacts {
    position: absolute;
    left: 687px;
    top: 146px;
    font-size: 39px;
    line-height: 38px;
  }
  .contact + .contact { margin-top: 26px; }
  .contact-name { display: block; color: var(--ink); }
  .contact-phone { display: block; color: var(--leaf); }
  .email {
    position: absolute;
    left: 298px;
    top: 42px;
    font-size: 38px;
    color: var(--on-leaf);
  }
</style>
</head>
<body>
  <main class="card">
    <svg class="top-tab" viewBox="0 0 148 70" aria-hidden="true">
      <polygon points="0,0 148,0 74,70" fill="var(--leaf)"/>
    </svg>

    <h1 class="company">
      <span class="company-line-1">Bramblewood</span>
      <span class="company-line-2">Yardworks</span>
    </h1>

    <div class="divider"></div>

    <section class="contacts">
      <p class="contact">
        <span class="contact-name">Owen Platt</span>
        <span class="contact-phone">555-273-9104,</span>
      </p>
      <p class="contact">
        <span class="contact-name">Daniel Korbin</span>
        <span class="contact-phone">555-618-3927</span>
      </p>
    </section>

    <footer class="footer-band">
      <svg class="footer-notch" viewBox="0 0 89 38" aria-hidden="true">
        <polygon points="0,0 89,0 44.5,38" fill="var(--card)"/>
      </svg>
      <p class="email">bramblewoodyard@mailvista.net</p>
    </footer>
  </main>
</body>
</html>
```